Medical Billing Company Needs a Business Card Design

We need a business card design for a Florida based medical billing company called 'Clinicians Keystone Solutions'. We specialize in providing revenue cycle management services to physician and therapist offices (we're basically their back-office processing partner for providing billing software, claims submissions, A/R follow-up and patient statements & collections. Our logo is red and blue-ish, so make sure that whatever other elements are used will match appropriately. Our current business card design has a too small font size. I'd like to project an image that shows we are modern & reliable. On a side note, I'm planning on using ZUB for printing these cards.

Target Market(s)

Office managers, physicians, therapists

Industry/Entity Type

Printing

Requirements
Must have
• Logo
Name of Employee
Phone
Fax
E-mail
Website

```html
<!DOCTYPE html>
<html lang="en">
<head>
<meta charset="UTF-8">
<title>Clinicians Keystone Solutions – Business Card</title>
<link rel="stylesheet" href="https://fonts.googleapis.com/css2?family=Open+Sans:wght@400;600;700&display=swap">
<style>
  :root {
    --canvas-bg: #e4e4ea;
    --card-bg: #ffffff;
    --navy: #2a1a6e;
    --band-deep: #1f0a63;
    --band-light: #5a47a8;
    --accent-red: #b2242c;
    --text-grey: #55545c;
    --name-violet: #4b3b94;
    --white: #ffffff;
  }
  * { box-sizing: border-box; margin: 0; padding: 0; }
  html, body {
    width: 1200px; height: 987px; overflow: hidden;
    background: var(--canvas-bg);
    font-family: "Open Sans", Arial, sans-serif;
  }
  .canvas { position: relative; width: 1200px; height: 987px; }

  .card {
    position: absolute;
    width: 700px; height: 400px;
    background: var(--card-bg);
    border-radius: 34px;
    overflow: hidden;
    box-shadow: 0 14px 30px rgba(40, 40, 70, 0.18);
  }
  .card--back { left: 430px; top: 60px; }
  .card--front { left: 70px; top: 520px; }

  .wordmark {
    display: flex; align-items: center; gap: 14px;
    color: var(--navy);
    font-weight: 400;
    font-size: 38px;
    letter-spacing: 2px;
    text-transform: uppercase;
    white-space: nowrap;
  }
  .wordmark__square {
    width: 22px; height: 22px;
    background: var(--accent-red);
  }

  .card--back .wordmark { position: absolute; left: 0; right: 0; top: 140px; justify-content: center; }
  .card--back .website {
    position: absolute; left: 0; right: 0; top: 220px;
    text-align: center;
    font-size: 22px; letter-spacing: 5px;
    color: var(--text-grey);
  }

  .card--front .wordmark { position: absolute; left: 48px; top: 52px; font-size: 34px; }

  .holder {
    position: absolute; right: 52px; top: 140px;
    font-size: 28px; color: var(--name-violet);
  }
  .holder__name { font-weight: 700; }
  .holder__title { font-weight: 400; color: var(--accent-red); }

  .band { position: absolute; inset: 0; }

  .contact {
    position: absolute; left: 40px; top: 258px;
    color: var(--white);
    font-size: 17px;
    line-height: 1;
    display: flex; flex-direction: column; gap: 14px;
  }
  .contact__row { display: flex; align-items: center; gap: 18px; }
  .contact__item { display: inline-flex; align-items: center; gap: 7px; }
  .contact__icon { width: 15px; height: 15px; flex: none; }
</style>
</head>
<body>
<main class="canvas">

  <section class="card card--back" aria-label="Card back">
    <div class="wordmark"><span class="wordmark__square"></span><span>Clinicians Keystone</span></div>
    <p class="website">www.clinicianskeystone.com</p>
  </section>

  <section class="card card--front" aria-label="Card front">
    <svg class="band" width="700" height="400" viewBox="0 0 700 400" aria-hidden="true">
      <defs>
        <radialGradient id="bandGlow" cx="0.45" cy="0.55" r="0.7">
          <stop offset="0" stop-color="var(--band-light)"/>
          <stop offset="1" stop-color="var(--band-deep)"/>
        </radialGradient>
      </defs>
      <path d="M0 200 Q380 215 700 400 L0 400 Z" fill="url(#bandGlow)"/>
      <path d="M0 192 Q385 205 700 388" fill="none" stroke="var(--accent-red)" stroke-width="3"/>
    </svg>

    <div class="wordmark"><span>Clinicians Keystone</span><span class="wordmark__square"></span></div>

    <p class="holder"><span class="holder__name">Your Name,</span> <span class="holder__title">Title</span></p>

    <div class="contact">
      <div class="contact__row"><span>Street Name, City Name, State Zip Code</span></div>
      <div class="contact__row">
        <span class="contact__item">
          <svg class="contact__icon" viewBox="0 0 16 16" aria-hidden="true"><path d="M4 1.5l2.2 3-1.4 1.6a8 8 0 0 0 5.1 5.1l1.6-1.4 3 2.2-1.2 2.4C7.5 14.5 1.5 8.5 1.6 2.7z" fill="none" stroke="currentColor" stroke-width="1.4"/></svg>
          123-456-0789
        </span>
        <span class="contact__item">
          <svg class="contact__icon" viewBox="0 0 16 16" aria-hidden="true"><rect x="4" y="1" width="8" height="14" rx="1.5" fill="none" stroke="currentColor" stroke-width="1.4"/><line x1="7" y1="12.5" x2="9" y2="12.5" stroke="currentColor" stroke-width="1.4"/></svg>
          123-456-0789
        </span>
      </div>
      <div class="contact__row">
        <span class="contact__item">
          <svg class="contact__icon" viewBox="0 0 16 16" aria-hidden="true"><rect x="1" y="3" width="14" height="10" rx="1" fill="none" stroke="currentColor" stroke-width="1.4"/><path d="M1.5 3.5L8 9l6.5-5.5" fill="none" stroke="currentColor" stroke-width="1.4"/></svg>
          info@clinicianskeystone.com
        </span>
      </div>
      <div class="contact__row">
        <span class="contact__item">
          <svg class="contact__icon" viewBox="0 0 16 16" aria-hidden="true"><circle cx="8" cy="8" r="6.5" fill="none" stroke="currentColor" stroke-width="1.3"/><ellipse cx="8" cy="8" rx="3" ry="6.5" fill="none" stroke="currentColor" stroke-width="1.1"/><line x1="1.5" y1="8" x2="14.5" y2="8" stroke="currentColor" stroke-width="1.1"/></svg>
          www.clinicianskeystone.com
        </span>
      </div>
    </div>
  </section>

</main>
</body>
</html>
```